Italian restaurant needs new site

Need to make our website better.

Must have reservation module

Must be able to sell wine tasting tours and wine pairing tours and intégrate with dunmo desk

Blog

Social media

Wandervane ranking and last review.
Updates

Number of Pages Required

1 page

Font styles to use
Serif

Requirements
Must have
• Reservation module
• Marketplace to buy wine pairings and gift certificates
• Wandervane review
• Kindlepost posts
• All info from old site

```html
<!DOCTYPE html>
<html lang="en">
<head>
<meta charset="utf-8">
<title>Verdello — Italian Restaurant</title>
<link href="https://fonts.googleapis.com/css2?family=Open+Sans:ital,wght@0,400;0,600;0,700;1,400&family=Playfair+Display:wght@400;700&family=Dancing+Script:wght@500;700&family=Raleway:wght@400;600;700&display=swap" rel="stylesheet">
<style>
:root{
  --accent:#f0a540;
  --accent-dark:#d98b22;
  --ink:#2b2b2b;
  --text:#5a5a5a;
  --muted:#9a9a9a;
  --line:#e6e6e6;
  --paper:#ffffff;
  --cream:#f7f3ee;
  --night:#2f2f2f;
  --night-2:#262626;
}
*{box-sizing:border-box;margin:0;padding:0}
html,body{width:1200px;height:4945px;overflow:hidden}
body{position:relative;background:var(--paper);font-family:"Open Sans",Arial,sans-serif;color:var(--text)}
.abs{position:absolute}
.fill{position:absolute}
.script{font-family:"Dancing Script",cursive;color:var(--muted)}
.heading{font-family:"Raleway",Arial,sans-serif;font-weight:700;letter-spacing:2px;color:var(--ink);text-transform:uppercase}
.center{text-align:center}

/* hero */
.hero{left:0;top:0;width:1200px;height:676px;background:radial-gradient(ellipse at 50% 45%,#3a3532 0%,#2a2624 55%,#4a3326 100%)}
.nav{left:0;top:30px;width:1200px;display:flex;justify-content:center;align-items:center;gap:28px;font:600 11px "Raleway",sans-serif;letter-spacing:1.5px;color:#fff}
.nav .on{color:var(--accent)}
.nav .brand{font:700 30px "Playfair Display",serif;letter-spacing:1px;margin:0 26px;color:#fff}
.nav .icons{display:flex;gap:14px;margin-left:6px}
.bistro{left:28px;top:20px;width:200px;height:120px;background:rgba(0,0,0,.55);padding:16px 18px;color:#fff}
.bistro b{font:400 26px "Playfair Display",serif;display:block}
.bistro small{font-size:9px;letter-spacing:2px;display:block;margin-top:4px;color:#d8d0c6}
.hero-copy{left:0;top:200px;width:1200px}
.hero-copy .script{font-size:34px;color:#fff}
.hero-title{font:700 50px "Playfair Display",serif;color:#fff;letter-spacing:6px;margin-top:4px}
.ribbon{display:inline-block;margin-top:14px;background:var(--accent);color:#fff;font:700 12px "Raleway",sans-serif;letter-spacing:3px;padding:7px 30px}
.btn{display:inline-block;background:var(--accent);color:#fff;font:700 11px "Raleway",sans-serif;letter-spacing:2px;padding:11px 28px}
.hero-copy .btn{margin-top:26px;display:block;width:140px;margin-left:auto;margin-right:auto}

/* reservation */
.reserve-title{left:0;top:742px;width:1200px;font:italic 13px "Open Sans";letter-spacing:4px;color:var(--muted)}
.reserve-sub{left:0;top:778px;width:1200px;font-size:9px;letter-spacing:2px;color:#b9b9b9}
.field{top:843px;height:30px;border-bottom:1px solid #cfcfcf;display:flex;align-items:center;gap:12px;font-size:13px;color:var(--ink)}
.find{left:530px;top:910px;width:140px;height:32px;background:var(--ink);color:#fff;font:700 11px "Raleway";letter-spacing:2px;display:flex;align-items:center;justify-content:center}
.note{left:150px;top:1030px;width:900px;font-size:14px;line-height:26px;color:var(--text)}

/* about */
.photo-a{left:0;top:1193px;width:597px;height:515px;background:linear-gradient(160deg,#6b5a4a,#3d3128 55%,#8a6a48)}
.photo-a span{position:absolute;left:60px;bottom:40px;font:700 46px/1.05 "Raleway",sans-serif;color:#fff;text-transform:uppercase;text-shadow:0 2px 6px rgba(0,0,0,.6)}
.about{left:603px;top:1193px;width:597px;height:515px}
.frame{position:absolute;inset:8px;border:2px solid var(--accent)}
.about .mark{left:268px;top:90px;width:60px;height:60px;border-radius:50%;background:#e8dcd0}
.about h2{position:absolute;left:0;top:200px;width:597px;font:400 34px "Raleway";letter-spacing:4px;color:var(--ink)}
.about p{position:absolute;left:90px;top:258px;width:417px;font-size:11px;line-height:18px;color:var(--muted)}
.about .btn{position:absolute;left:240px;top:382px;padding:8px 20px}

/* deal */
.deal{left:0;top:1708px;width:597px;height:534px}
.deal .script{position:absolute;top:50px;width:597px;font-size:20px}
.deal h3{position:absolute;top:80px;width:597px;font-size:18px}
.deal p{position:absolute;left:110px;top:118px;width:377px;font-size:11px;line-height:17px;color:var(--muted)}
.price{position:absolute;left:0;top:208px;width:597px;font:700 24px "Open Sans";color:var(--accent)}
.timer{position:absolute;left:118px;top:262px;display:flex;gap:24px}
.timer div{width:62px;height:62px;border:2px solid var(--accent);border-radius:50%;display:flex;flex-direction:column;align-items:center;justify-content:center;font:700 20px "Open Sans";color:var(--ink)}
.timer small{font:400 8px "Open Sans";letter-spacing:1px;color:var(--muted)}
.deal .dish{left:200px;top:370px;width:200px;height:130px;border-radius:50% 50% 45% 45%;background:linear-gradient(#e9d7bd,#2f5aa8 70%)}
.tile{width:301px;height:267px}

/* products */
.feat-icon{left:580px;top:2290px;width:40px;height:24px}
.feat-script{left:0;top:2318px;width:1200px;font-size:18px}
.feat-title{left:0;top:2344px;width:1200px;font-size:18px}
.filters{left:0;top:2393px;width:1200px;display:flex;justify-content:center;gap:14px;font:600 10px "Raleway";letter-spacing:1.5px;color:var(--muted)}
.filters .on{color:var(--accent)}
.card{width:268px}
.card .pic{height:290px;background:var(--paper)}
.card .pic i{position:absolute;left:30px;right:30px;top:60px;bottom:50px;border-radius:10px}
.stars{margin-top:14px;text-align:center;color:var(--accent);font-size:12px;letter-spacing:2px}
.card .name{margin-top:8px;text-align:center;font:600 11px "Raleway";letter-spacing:1px;color:var(--ink)}
.card .cost{margin-top:4px;text-align:center;font-size:12px;color:var(--accent)}
.card.active{box-shadow:0 4px 18px rgba(0,0,0,.15);background:var(--paper);padding-bottom:0}
.actions{display:flex;height:50px;margin-top:14px;background:var(--accent)}
.actions span{flex:1;display:flex;align-items:center;justify-content:center;border-right:1px solid rgba(255,255,255,.3);color:#fff;font:700 9px "Raleway";letter-spacing:1px}
.actions span.mid{background:var(--ink)}
.sale{position:absolute;left:0;top:0;width:0;height:0;border-top:48px solid #e84b3a;border-right:48px solid transparent}

/* testimonial */
.store{left:0;top:3313px;width:597px;height:528px;background:linear-gradient(150deg,#5a4634,#2b221b 60%,#6d5138)}
.store .script{position:absolute;top:110px;width:597px;font-size:34px;color:#fff}
.store p{position:absolute;left:80px;top:165px;width:437px;font:italic 14px/24px "Open Sans";color:#eee}
.avatars{position:absolute;left:210px;top:290px;display:flex;gap:22px;align-items:center}
.avatars i{width:46px;height:46px;border-radius:50%;background:#c9b49c;border:3px solid #fff}
.avatars i.big{width:78px;height:78px;background:#b8a088}
.store .who{position:absolute;top:388px;width:597px;font:italic 13px "Open Sans";color:#fff}
.store .role{position:absolute;top:410px;width:597px;font-size:10px;color:#cfc3b5}
.customers{left:597px;top:3313px;width:603px;height:528px}
.customers .script{position:absolute;top:64px;width:603px;font-size:16px}
.customers h3{position:absolute;top:86px;width:603px;font-size:18px}
.customers p{position:absolute;left:130px;top:120px;width:343px;font-size:11px;line-height:17px;color:var(--muted)}
.review{position:absolute;left:130px;top:170px;width:343px;height:320px;border:1px solid var(--line);background:#fafafa}
.review b{display:block;padding:10px 14px;font:700 13px "Open Sans";color:#3e8f4f;border-bottom:1px solid var(--line)}
.review .rows{position:absolute;left:14px;right:14px;top:50px;bottom:14px;background:linear-gradient(#eef0ee,#f8f8f8)}

/* social */
.post{left:30px;top:3870px;width:540px;height:462px;border:1px solid #d8d8d8;background:#fff}
.post .bar{height:44px;display:flex;align-items:center;gap:12px;padding:0 14px;border-bottom:1px solid var(--line);font-size:14px;color:#333}
.post .bar span{background:#4a67a8;color:#fff;font:700 11px "Open Sans";padding:4px 10px}
.post .body{position:absolute;left:14px;right:14px;top:58px;bottom:50px;background:linear-gradient(#f2f2f2,#dfe4ea)}
.post .foot{position:absolute;left:14px;bottom:14px;font-size:12px;color:#4a67a8}
.meal{left:597px;top:3841px;width:603px;height:517px;background:linear-gradient(140deg,#e9e2d8,#7a5a3c 55%,#2f2420)}
.meal .cap{position:absolute;left:0;right:0;bottom:70px;height:36px;background:rgba(0,0,0,.55);color:#fff;font-size:14px;display:flex;align-items:center;justify-content:center}

/* bottom trio */
.recipe{left:0;top:4358px;width:400px;height:284px;background:#fff}
.recipe .pic{left:110px;top:0;width:290px;height:284px;background:linear-gradient(160deg,#e8e1d8,#8a5a34 60%,#efe8e0)}
.recipe .script{position:absolute;left:22px;top:180px;font-size:16px;color:var(--ink)}
.recipe h4{position:absolute;left:22px;top:205px;font:700 26px "Raleway";color:var(--accent);letter-spacing:1px}
.brandbox{left:400px;top:4358px;width:400px;height:284px;background:linear-gradient(#3b3b3b,#2a2a2a)}
.brandbox .name{position:absolute;top:36px;width:400px;font:700 30px "Playfair Display",serif;color:#fff}
.brandbox .tag{position:absolute;top:78px;width:400px;font-size:8px;letter-spacing:3px;color:#bbb}
.brandbox p{position:absolute;left:50px;top:100px;width:300px;font-size:10px;line-height:16px;color:#cfcfcf}
.soc{position:absolute;top:162px;left:0;width:400px;display:flex;justify-content:center;gap:10px}
.soc i{width:22px;height:22px;border-radius:50%;border:1px solid #888}
.brandbox .orn{left:160px;top:205px;width:80px;height:50px;background:rgba(255,255,255,.08);border-radius:40px}
.good{left:800px;top:4358px;width:400px;height:284px;background:#fff}
.good .pic{left:230px;top:50px;width:170px;height:234px;background:linear-gradient(#d9a66a,#8a5528)}
.good .love{left:270px;top:14px;width:66px;height:66px;border-radius:50%;background:var(--accent);color:#fff;font:700 18px "Dancing Script",cursive;display:flex;align-items:center;justify-content:center}
.good .script{position:absolute;left:30px;top:160px;font-size:16px}
.good h4{position:absolute;left:30px;top:182px;font:700 26px "Raleway";color:var(--ink)}
.good p{position:absolute;left:30px;top:222px;width:190px;font-size:10px;line-height:15px;color:var(--muted)}

/* footer */
.footer{left:0;top:4642px;width:1200px;height:303px;background:var(--night)}
.fcol{position:absolute;top:40px;color:#bdbdbd;font-size:11px;line-height:19px}
.fcol h5{font:700 12px "Raleway";letter-spacing:1.5px;color:#fff;margin-bottom:14px}
.tags{display:flex;flex-wrap:wrap;gap:6px;width:160px}
.tags span{border:1px solid #555;padding:1px 8px;font-size:10px}
.links{display:grid;grid-template-columns:90px 90px}
.hours{width:220px}
.hours div{display:flex;justify-content:space-between;border-bottom:1px solid #444}
.hours .badge{margin-top:10px;width:110px;padding:6px;background:#fff;color:var(--ink);font-size:10px;text-align:center}
</style>
</head>
<body>

<!-- HERO -->
<section class="abs hero" role="img" aria-label="Dark kitchen table with bread, spices, tomatoes and cutlery around the edges"></section>
<div class="abs bistro"><b>Lumera</b><small>BISTRO · ITALIAN CUISINE &amp; WINE BAR</small></div>
<nav class="abs nav">
  <span class="on">HOME</span><span>OUR STORY</span><span>SHOP</span>
  <span class="brand">Verdello</span>
  <span>MENU</span><span>BLOG</span><span>CONTACT</span>
  <span class="icons">
    <svg width="12" height="12" viewBox="0 0 12 12"><circle cx="5" cy="5" r="3.8" fill="none" stroke="#fff" stroke-width="1.4"/><path d="M8 8l3 3" stroke="#fff" stroke-width="1.4"/></svg>
    <svg width="13" height="12" viewBox="0 0 13 12"><path d="M1 1h2l2 7h6l1.5-5H4" fill="none" stroke="#fff" stroke-width="1.3"/><circle cx="5.5" cy="10.5" r="1" fill="#fff"/><circle cx="10" cy="10.5" r="1" fill="#fff"/></svg>
  </span>
</nav>
<div class="abs hero-copy center">
  <div class="script">Different types of</div>
  <div class="hero-title">ITALIAN CUISINE</div>
  <div class="ribbon">SINCE 1990</div>
  <span class="btn">SHOP NOW</span>
</div>

<!-- RESERVATION -->
<div class="abs reserve-title center">MAKE A RESERVATION</div>
<div class="abs reserve-sub center">BOOKING BY DUNMO DESK</div>
<div class="abs field" style="left:265px;width:135px">
  <svg width="14" height="14" viewBox="0 0 14 14"><rect x="1" y="2" width="12" height="11" fill="none" stroke="#333"/><path d="M1 5h12" stroke="#333"/></svg>08/05/2017</div>
<div class="abs field" style="left:510px;width:170px;justify-content:space-between">
  <span style="display:flex;gap:12px;align-items:center"><svg width="14" height="14" viewBox="0 0 14 14"><circle cx="7" cy="7" r="6" fill="none" stroke="#333"/><path d="M7 3v4h3" fill="none" stroke="#333"/></svg>7:00 pm</span><span>▾</span></div>
<div class="abs field" style="left:720px;width:200px;justify-content:space-between">
  <span style="display:flex;gap:12px;align-items:center"><svg width="12" height="14" viewBox="0 0 12 14"><circle cx="6" cy="4" r="3" fill="#333"/><path d="M0 14c0-4 3-6 6-6s6 2 6 6z" fill="#333"/></svg>2 People</span><span>▾</span></div>
<div class="abs find">FIND A TABLE</div>
<p class="abs note center">Due to the limited amount of tables in our restaurant, we cannot guarantee a private table. Some reservations will be sat at the bar or communal. If you prefer a table, please call or make a note and we will do our best to accommodate your request.</p>
<svg class="abs" style="left:588px;top:1104px" width="24" height="12" viewBox="0 0 24 12"><path d="M2 6h20M6 2L2 6l4 4M18 2l4 4-4 4" fill="none" stroke="#aaa"/></svg>

<!-- ABOUT -->
<div class="abs photo-a" role="img" aria-label="Restaurant interior with pendant lamps, brick wall and bar counter"><span>Image of your<br>restaurant</span></div>
<section class="abs about center">
  <div class="frame"></div>
  <div class="fill mark" role="img" aria-label="Small illustration of a waiter carrying a tray"></div>
  <h2>·ABOUT·</h2>
  <p>Our family kitchen has served honest Italian food since 1990. We bake our bread every morning, make fresh pasta by hand and pour wines from small vineyards we know well. Join us for a quiet dinner, a wine tasting tour or a long Sunday lunch with friends and family.</p>
  <span class="btn">READ MORE</span>
</section>

<!-- DEAL -->
<section class="abs deal center">
  <div class="script">Special weekly bonus</div>
  <h3 class="heading">Deal of the day</h3>
  <p>A basket of warm rolls, aged cheese and a glass of house red, paired by our sommelier. Offer ends when the timer below runs out.</p>
  <div class="price">$29.00</div>
  <div class="timer"><div>01<small>DAYS</small></div><div>16<small>HOURS</small></div><div>53<small>MINS</small></div><div>48<small>SECS</small></div></div>
  <div class="fill dish" role="img" aria-label="Blue bowl filled with assorted cookies and nuts"></div>
</section>
<div class="abs tile" style="left:597px;top:1708px;background:linear-gradient(135deg,#2f3b4a,#c6a27c 60%,#3a4350)" role="img" aria-label="Bowls of flour, eggs and spices on a dark table"></div>
<div class="abs tile" style="left:898px;top:1708px;background:#fff;border:1px solid var(--line)">
  <div class="abs" style="left:100px;top:85px;width:100px;height:100px;background:#ece6de;transform:rotate(45deg)" role="img" aria-label="Bakery badge"></div>
</div>
<div class="abs tile" style="left:597px;top:1975px;background:radial-gradient(circle at 50% 50%,#e0a25a,#c45a32 45%,#efe8df 70%)" role="img" aria-label="Fresh pizza with basil on a light surface"></div>
<div class="abs tile" style="left:898px;top:1975px;background:linear-gradient(120deg,#e7d7b8,#b07a44 55%,#6a4428)" role="img" aria-label="Flour on a board beside a loaf of rustic bread"></div>

<!-- FEATURED PRODUCTS -->
<svg class="abs feat-icon" viewBox="0 0 40 24"><path d="M20 4c-6 0-9 6-9 10h18c0-4-3-10-9-10zM8 18h24" fill="none" stroke="#aaa" stroke-width="1.5"/></svg>
<div class="abs script feat-script center">Organic products</div>
<h3 class="abs heading feat-title center">Featured products</h3>
<div class="abs filters"><span class="on">ALL PRODUCTS</span>/<span>BREADS</span>/<span>CAKES</span>/<span>COOKIES</span>/<span>FLOUR</span>/<span>OTHER</span></div>

<div class="abs card" style="left:30px;top:2450px"><div class="pic" style="position:relative"><i role="img" aria-label="Row of cookies" style="background:linear-gradient(#fff,#d9b48a 60%,#fff)"></i></div><div class="stars">★★★★☆</div><div class="name">COOKIES COMBO</div><div class="cost">$12.99</div></div>
<div class="abs card active" style="left:327px;top:2440px"><div class="pic" style="position:relative"><span class="sale"></span><i role="img" aria-label="Sliced pizza with tomatoes" style="background:radial-gradient(#e7a055,#c0552f 60%,#fff 75%)"></i></div><div class="stars">★★★★☆</div><div class="actions"><span>♡</span><span class="mid">ADD TO CART</span><span>⇄</span><span>⌕</span></div></div>
<div class="abs card" style="left:624px;top:2450px"><div class="pic" style="position:relative"><i role="img" aria-label="Caprese platter on a wooden board" style="background:linear-gradient(#fff,#8a6a48 40%,#c84030 60%,#fff)"></i></div><div class="stars">★★★★☆</div><div class="name">CINNAMON BUNS</div><div class="cost">$12.99</div></div>
<div class="abs card" style="left:921px;top:2450px"><div class="pic" style="position:relative"><i role="img" aria-label="Stack of brown bread loaves" style="background:linear-gradient(#fff,#b58356 45%,#7a5234)"></i></div><div class="stars">★★★★☆</div><div class="name">BROWN BREADS COMBO</div><div class="cost">$12.99</div></div>

<div class="abs card" style="left:30px;top:2850px"><div class="pic" style="position:relative"><i role="img" aria-label="Olives and cheese on a wooden board" style="background:linear-gradient(#fff,#caa06c 45%,#5b6a34)"></i></div><div class="stars">★★★★☆</div><div class="name">CHOCOLATE CHIP COOKIES</div><div class="cost">$12.99</div></div>
<div class="abs card" style="left:327px;top:2850px"><div class="pic" style="position:relative"><i role="img" aria-label="Sack of flour with wheat" style="background:linear-gradient(#fff,#d8c09a 50%,#a57a48)"></i></div><div class="stars">★★★★☆</div><div class="name">BAKING FLOUR</div><div class="cost">$12.99</div></div>
<div class="abs card" style="left:624px;top:2850px"><div class="pic" style="position:relative"><i role="img" aria-label="Pizza slices on a plate" style="background:radial-gradient(#e9b067,#c95b33 60%,#fff 75%)"></i></div><div class="stars">★★★★☆</div><div class="name">SWEET ALMONDS</div><div class="cost">$12.99</div></div>
<div class="abs card" style="left:921px;top:2850px"><div class="pic" style="position:relative"><i role="img" aria-label="Cup of cookie ice cream" style="background:linear-gradient(#fff,#d9c6a8 40%,#5a3a28)"></i></div><div class="stars">★★★★☆</div><div class="name">COOKIE ICE-CREAM</div><div class="cost">$12.99</div></div>

<!-- TESTIMONIAL -->
<section class="abs store center" role="img" aria-label="Chocolate cookies on a dark wooden table">
  <div class="script">The best organic store!</div>
  <p>Wonderful food, fresh bread and the kindest team in town. We come back every week for the pasta and always leave with a loaf for home.</p>
  <div class="avatars"><i></i><i class="big"></i><i></i></div>
  <div class="who">Marco Bellini</div>
  <div class="role">Regular guest</div>
</section>
<section class="abs customers center">
  <div class="script">They trust us</div>
  <h3 class="heading">Our customers</h3>
  <p>See our ranking and the latest guest reviews shared on Wandervane.</p>
  <div class="review" role="img" aria-label="Wandervane ranking panel with recent guest reviews">
    <b style="text-align:left">Wandervane</b><div class="rows"></div>
  </div>
</section>

<!-- SOCIAL -->
<section class="abs post" role="img" aria-label="Latest Kindlepost post with promotional image">
  <div class="bar"><span>Like</span>You like this.</div>
  <div class="body"></div>
  <div class="foot">Kindlepost</div>
</section>
<section class="abs meal" role="img" aria-label="Pan of baked eggs and vegetables on a kitchen counter">
  <div class="cap">Today's first meal of the day almost ready</div>
</section>

<!-- BOTTOM TRIO -->
<section class="abs recipe">
  <div class="fill pic" role="img" aria-label="Bowl of roasted meat and vegetables"></div>
  <div class="script">the recipe of</div>
  <h4>WINTER AUTUMN</h4>
</section>
<section class="abs brandbox center">
  <div class="name">Verdello</div>
  <div class="tag">ORGANIC STORE</div>
  <p>Fresh bread, fine wines and seasonal plates made with care. Visit us for tasting tours, pairings and gift certificates.</p>
  <div class="soc"><i></i><i></i><i></i><i></i><i></i></div>
  <div class="fill orn" role="img" aria-label="Olive branch ornament"></div>
</section>
<section class="abs good">
  <div class="fill pic" role="img" aria-label="Hand holding a bread roll"></div>
  <div class="fill love">love</div>
  <div class="script">a taste of life</div>
  <h4>GOOD LIFE</h4>
  <p>Simple food shared with good people.</p>
</section>

<!-- FOOTER -->
<footer class="abs footer">
  <div class="fcol" style="left:230px">
    <h5>CONTACT</h5>
    <div>Main</div><div>14 Via Lumera, Suite 3</div><div>Greenvale, NY 10457</div><div>(555) 014-2290</div>
    <div style="margin-top:8px">Store</div><div>22 Olive Street, Greenvale</div><div>hello@verdello.test</div>
  </div>
  <div class="fcol" style="left:420px">
    <h5>POPULAR TAGS</h5>
    <div class="tags"><span>bread</span><span>wine pairing</span><span>pasta</span><span>gift cards</span><span>tasting</span><span>cakes</span><span>flour</span><span>organic</span></div>
  </div>
  <div class="fcol" style="left:610px">
    <h5>USEFUL LINK</h5>
    <div class="links"><span>My account</span><span>News</span><span>Shop</span><span>Orders</span><span>Wine tours</span><span>Returns</span><span>Our story</span><span>FAQ</span><span>Contact</span><span>Privacy</span></div>
  </div>
  <div class="fcol" style="left:800px">
    <h5>WORKING TIME</h5>
    <div class="hours">
      <div><span>Monday – Friday</span><span>08:00am – 10:00pm</span></div>
      <div><span>Saturday</span><span>09:00am – 11:00pm</span></div>
      <div><span>Sunday</span><span>10:00am – 09:00pm</span></div>
      <div class="badge">Happy hours 5–7pm</div>
    </div>
  </div>
</footer>

</body>
</html>
```